Specialised investor in e-mobility and energy wants business card design

We need a business card design that fits our existing corporate design. <The look and feel must be 'sharp'/'clean', dynamic, communicate momentum, professionalism etc (as one would imagine from a firm in the financial sector). We like the idea of a reverse-side of the card that includes the logo, and the name and contact details on the other. We expect the deliverable to be whatever format might be required to be able to get cards printed directly by a service such as kelmo press. Our website is www.zub.capital

```html
<!DOCTYPE html>
<html lang="en">
<head>
<meta charset="utf-8">
<title>Zub Capital – Business Card</title>
<link href="https://fonts.googleapis.com/css2?family=Montserrat:wght@400;500;700&display=swap" rel="stylesheet">
<style>
  :root {
    --bg: #e9eaec;
    --card-white: #ffffff;
    --brand-green: #88b34b;
    --brand-dark: #2f5420;
    --ink: #1d1d1d;
    --shadow: rgba(0, 0, 0, 0.14);
  }
  * { box-sizing: border-box; margin: 0; padding: 0; }
  html, body {
    width: 1200px; height: 900px; overflow: hidden;
    background: var(--bg);
    font-family: "Montserrat", sans-serif;
  }
  .sheet {
    position: relative; width: 1200px; height: 900px;
    display: flex; align-items: center; justify-content: center; gap: 40px;
  }
  .card {
    position: relative; width: 540px; height: 350px;
    box-shadow: 0 10px 28px var(--shadow);
  }
  .card--front {
    background: var(--brand-green);
    display: flex; align-items: center; justify-content: center;
  }
  .card--back { background: var(--card-white); }

  .wordmark {
    display: flex; align-items: center; gap: 14px;
    color: var(--brand-dark); font-weight: 500; letter-spacing: 0.5px;
  }
  .wordmark__dot { border-radius: 50%; background: var(--brand-dark); }
  .card--front .wordmark { font-size: 58px; }
  .card--front .wordmark__dot { width: 26px; height: 26px; }
  .card--back .wordmark {
    position: absolute; top: 40px; right: 40px;
    font-size: 34px; gap: 10px;
  }
  .card--back .wordmark__dot { width: 16px; height: 16px; }

  .address {
    position: absolute; top: 150px; right: 40px;
    text-align: right; font-size: 14px; line-height: 1.45; color: var(--ink);
  }
  .person { position: absolute; top: 150px; left: 40px; }
  .person__name {
    font-size: 18px; font-weight: 700; letter-spacing: 0.6px;
    color: var(--brand-green); text-transform: uppercase;
  }
  .person__role { font-size: 15px; color: var(--ink); margin-top: 2px; }

  .contacts {
    position: absolute; left: 40px; bottom: 36px;
    list-style: none; font-size: 14px; color: var(--ink);
  }
  .contacts li { display: flex; align-items: center; gap: 10px; line-height: 1.6; }
  .contacts svg { width: 13px; height: 13px; fill: var(--brand-green); flex: none; }
</style>
</head>
<body>
<main class="sheet">
  <section class="card card--front" aria-label="Card front">
    <div class="wordmark"><span class="wordmark__dot"></span>zub capital</div>
  </section>

  <section class="card card--back" aria-label="Card back">
    <div class="wordmark"><span class="wordmark__dot"></span>zub capital</div>

    <address class="address" style="font-style:normal">
      Zub Capital S.A.<br>Geneva, Switzerland
    </address>

    <div class="person">
      <p class="person__name">Aaron Velling</p>
      <p class="person__role">team directly</p>
    </div>

    <ul class="contacts">
      <li>
        <svg viewBox="0 0 24 24"><path d="M6.6 10.8a15 15 0 0 0 6.6 6.6l2.2-2.2a1 1 0 0 1 1-.25 11.4 11.4 0 0 0 3.6.57 1 1 0 0 1 1 1V20a1 1 0 0 1-1 1A17 17 0 0 1 3 4a1 1 0 0 1 1-1h3.5a1 1 0 0 1 1 1c0 1.25.2 2.45.57 3.6a1 1 0 0 1-.25 1z"/></svg>
        +41 79555 0184
      </li>
      <li>
        <svg viewBox="0 0 24 24"><path d="M2 5h20v14H2z M2 5l10 8 10-8" /></svg>
        aaron@zub.capital
      </li>
      <li>
        <svg viewBox="0 0 24 24"><circle cx="12" cy="12" r="10"/></svg>
        www.zub.capital
      </li>
    </ul>
  </section>
</main>
</body>
</html>
```